Every Shelf Set Neatly or ESN Organized needs a business card design. ESN Organized is a professi

We need a business card design that is clean, sharp and conveys a sense of organization. I already have a logo.

Target Market(s)

Families (specifically mothers), small business owners, parents, seniors

Industry/Entity Type

Business

Contact Information for Business Card

My website is www.esnorganized-example.com and my Facebook page is http://www.sociallink-example.com/everyshelfsetneatly. The phone number is 418-552-7094 and I want to be listed as Lorna M. Pelham, Owner

Requirements
Must have
• My logo.

```html
<!DOCTYPE html>
<html lang="en">
<head>
<meta charset="utf-8">
<title>ESN Organized – Business Card</title>
<link rel="stylesheet" href="https://fonts.googleapis.com/css2?family=Lato:wght@400;700&family=Raleway:wght@400;500&display=swap">
<style>
  :root {
    --stage: #e9e7e3;
    --card-white: #ffffff;
    --card-black: #0b0b0c;
    --brand-blue: #1a7fd4;
    --ink-dark: #1c1c1c;
    --ink-grey: #8c8c8c;
    --ink-light: #e6e6e6;
  }
  * { margin: 0; padding: 0; box-sizing: border-box; }
  html, body { width: 1200px; height: 950px; overflow: hidden; }
  body {
    background: var(--stage);
    font-family: "Lato", Arial, sans-serif;
    position: relative;
  }
  .card {
    position: absolute;
    left: 280px;
    width: 640px;
    height: 366px;
    border-radius: 4px;
    overflow: hidden;
    box-shadow: 0 10px 28px rgba(0,0,0,.22);
  }
  .card--front { top: 70px; background: var(--card-white); }
  .card--back  { top: 500px; background: var(--card-black); }

  .wordmark {
    font-family: "Raleway", Arial, sans-serif;
    font-weight: 500;
    letter-spacing: 3px;
    white-space: nowrap;
  }
  .card--front .wordmark {
    position: absolute;
    left: 0; right: 0; top: 130px;
    text-align: center;
    font-size: 34px;
    color: var(--ink-dark);
  }
  .card--front .wordmark .mark-dot {
    display: inline-block;
    width: 18px; height: 18px;
    border-radius: 50%;
    background: var(--brand-blue);
    margin-right: 14px;
    vertical-align: 3px;
  }
  .front-url {
    position: absolute;
    left: 0; right: 0; top: 210px;
    text-align: center;
    font-size: 15px;
    letter-spacing: 6px;
    color: var(--ink-dark);
  }

  .card--back .wordmark {
    position: absolute;
    left: 40px; top: 40px;
    font-size: 28px;
    color: var(--ink-light);
  }
  .card--back .wordmark .mark-dot {
    display: inline-block;
    width: 15px; height: 15px;
    border-radius: 50%;
    background: var(--brand-blue);
    margin-right: 12px;
    vertical-align: 2px;
  }
  .holder { position: absolute; left: 40px; top: 118px; }
  .holder-name { font-size: 22px; font-weight: 700; color: var(--brand-blue); }
  .holder-role { font-size: 15px; color: var(--ink-grey); margin-top: 2px; }

  .contact-list {
    position: absolute;
    left: 40px; top: 186px;
    list-style: none;
  }
  .contact-item {
    display: flex;
    align-items: center;
    gap: 10px;
    font-size: 16px;
    color: var(--ink-light);
    height: 26px;
  }
  .contact-icon { width: 15px; height: 15px; flex: none; }
  .icon-square {
    width: 14px; height: 14px;
    background: var(--brand-blue);
    border-radius: 2px;
    flex: none;
  }
  .corner-band {
    position: absolute;
    right: 0; bottom: 0;
    width: 380px; height: 220px;
  }
</style>
</head>
<body>
  <section class="card card--front" aria-label="Business card front">
    <div class="wordmark"><span class="mark-dot"></span>Every Shelf Set Neatly</div>
    <p class="front-url">www.esnorganized-example.com</p>
  </section>

  <section class="card card--back" aria-label="Business card back">
    <div class="wordmark"><span class="mark-dot"></span>Every Shelf Set Neatly</div>

    <div class="holder">
      <p class="holder-name">Lorna M. Pelham</p>
      <p class="holder-role">Owner</p>
    </div>

    <ul class="contact-list">
      <li class="contact-item">
        <svg class="contact-icon" viewBox="0 0 16 16" aria-hidden="true">
          <circle cx="8" cy="8" r="8" fill="var(--brand-blue)"/>
          <path d="M5 4.5c.5-.4 1-.3 1.3.2l.6 1.2c.2.4.1.8-.2 1l-.5.4c.4.9 1.2 1.8 2.2 2.3l.4-.5c.3-.3.7-.4 1-.2l1.2.6c.5.3.6.8.2 1.3-.6.8-1.5 1-2.4.6C7 10.7 5.3 9 4.6 7c-.3-.9-.2-1.8.4-2.5z" fill="#0b0b0c"/>
        </svg>
        418-552-7094
      </li>
      <li class="contact-item">
        <svg class="contact-icon" viewBox="0 0 16 16" aria-hidden="true">
          <circle cx="8" cy="8" r="7" fill="none" stroke="var(--brand-blue)" stroke-width="1.5"/>
          <ellipse cx="8" cy="8" rx="3" ry="7" fill="none" stroke="var(--brand-blue)" stroke-width="1.2"/>
          <line x1="1" y1="8" x2="15" y2="8" stroke="var(--brand-blue)" stroke-width="1.2"/>
        </svg>
        www.esnorganized-example.com
      </li>
      <li class="contact-item">
        <span class="icon-square" aria-hidden="true"></span>
        everyshelfsetneatly
      </li>
    </ul>

    <svg class="corner-band" viewBox="0 0 380 220" aria-hidden="true">
      <path d="M0 220 L380 10 L380 220 Z" fill="var(--brand-blue)"/>
    </svg>
  </section>
</body>
</html>
```